Web Design Project

We need a web design company for a company based in London. We are an online minicab booking service that produces real time quotes on cab journey for consumers. Our colours are currently red and yellow, but do not need to stay that way; it's open to interpretation. Please avoid yellow and black as a colour combination. Our current site is: www.rovelink.co.uk We are looking for a new site to be user-friendly and easy to use, but more polished and professional looking, without using it usability and simplicity. We need to keep the booking capability on each page and it needs to draw in the user's eye. We need a site that is reliable and easy to use, but also fun.

Main objective: keep it simple, like it is now, but polish it up some. Also, we need to be able to add more content to it. And, we will also be adding a login capability for return users.

Target Market(s)

Internet-savvy people aged 18 and older.

Industry/Entity Type

It Company

Requirements
Must have
• Must have the booking widget. However, it doesn't have to be as large as it is now. We are actually thinking to split it over two pages. We will add a few options to the booking widget, such as another via option. The booking widget must be the most noticeable feature on the page. Sans serif font, please.
Should not have
• Should not be too busy and distracting. Please do not use any images of traditional taxis, ie. black cabs from London or yellow cabs from NYC. Our cars do not resemble these and our business cannot be associated with these images.

```html
<!DOCTYPE html>
<html lang="en">
<head>
<meta charset="utf-8">
<title>Rovelink – Online Minicab Booking</title>
<link rel="stylesheet" href="https://fonts.googleapis.com/css2?family=PT+Sans+Narrow:wght@400;700&family=Questrial&family=Tinos&display=swap">
<style>
:root{
  --red:#c20b0d;
  --red-dark:#9c0508;
  --plum:#4f0a34;
  --tab-red:#c8161c;
  --tab-mid:#7c1022;
  --tab-dark:#5c0d2a;
  --field-bg:#f4f4f8;
  --field-line:#b9b9c6;
  --cyan:#6ee4ff;
  --yellow:#ffd52b;
  --title-red:#b30d12;
  --text-grey:#4a4a4a;
  --story-blue:#2c4ad8;
  --fees-blue:#6a74b6;
  --link-plum:#4a0a2c;
  --white:#ffffff;
}
*{margin:0;padding:0;box-sizing:border-box}
html,body{width:1024px;height:1200px;overflow:hidden;background:var(--white)}
body{position:relative;font-family:"PT Sans Narrow",sans-serif;color:var(--text-grey)}
.frame{position:absolute;left:10px;top:0;width:1005px;height:1200px;border-left:1px solid #e4e4e4;border-right:1px solid #e4e4e4}

/* header */
.site-header{position:absolute;left:17px;top:0;width:992px;height:107px;background:linear-gradient(180deg,#d10f10,var(--red) 60%,var(--red-dark))}
.brand{position:absolute;left:14px;top:40px;display:flex;align-items:center;gap:10px}
.brand-dot{width:30px;height:30px;border-radius:50%;background:var(--white)}
.brand-name{font-family:"PT Sans Narrow",sans-serif;font-weight:700;font-size:46px;color:var(--white);line-height:1}
.booking-line{position:absolute;right:26px;top:50px;color:var(--white);white-space:nowrap}
.booking-line .number{font-size:34px}
.booking-line .label{font-size:24px}
.car-icon{position:absolute;right:42px;top:12px}

/* nav */
.main-nav{position:absolute;left:17px;top:107px;width:992px;height:59px;background:var(--plum)}
.main-nav ul{position:absolute;left:524px;top:19px;list-style:none;display:flex}
.main-nav li{height:40px;line-height:46px;padding:0 18px;color:var(--white);font-size:13px}
.main-nav li.active{background:var(--white);color:#222;border-radius:4px 4px 0 0;padding:0 21px}

/* hero */
.hero-photo{position:absolute;left:17px;top:176px;width:992px;height:385px;background:linear-gradient(180deg,#3d4c8e 0%,#5564a6 35%,#7a6f8a 62%,#3a3340 85%,#1f1d28 100%)}
.hero-tagline{position:absolute;left:434px;top:432px;font-family:"Tinos",serif;color:var(--white);text-shadow:0 1px 3px rgba(0,0,0,.5);line-height:38px}
.hero-tagline .line-1{font-size:35px;display:block}
.hero-tagline .line-2{font-size:30px;display:block}

/* booking widget */
.booking-tabs{position:absolute;left:47px;top:131px;display:flex;height:45px}
.booking-tabs span{display:block;height:45px;line-height:50px;color:var(--white);font-size:13px;text-align:center}
.tab-book{width:96px;background:var(--tab-red);border-radius:4px 0 0 0}
.tab-tour{width:111px;background:var(--tab-mid)}
.tab-account{width:111px;background:var(--tab-dark);border-radius:0 4px 0 0}
.booking-panel{position:absolute;left:47px;top:176px;width:318px;height:356px;background:rgba(255,255,255,.72);border-radius:0 0 6px 6px}
.field{position:absolute;height:32px;background:var(--field-bg);border:1px solid var(--field-line);font-size:11px;color:#3a0a20;line-height:30px;padding-left:11px}
.field svg{position:absolute;right:8px;top:8px}
.f-from{left:14px;top:21px;width:274px}
.f-to{left:14px;top:62px;width:274px}
.f-date{left:14px;top:103px;width:274px}
.f-pass{left:14px;top:144px;width:164px}
.f-kids{left:184px;top:144px;width:104px}
.contact-box{position:absolute;left:18px;top:196px;width:264px;height:142px;background:var(--white);border-radius:5px}
.contact-field{position:absolute;left:14px;width:228px;height:27px;background:var(--cyan);font-size:11px;color:#2b1838;line-height:26px;padding-left:14px}
.cf-name{top:23px}.cf-addr{top:53px}.cf-phone{top:84px}
.enter-button{position:absolute;left:224px;top:322px;width:80px;height:24px;background:var(--yellow);border-radius:7px;font-size:13px;color:#222;text-align:center;line-height:24px}

/* features strip */
.features{position:absolute;left:17px;top:569px;width:990px;height:164px;background:linear-gradient(180deg,#f2f2f2,#fafafa 50%,#ececec);border-radius:4px;box-shadow:0 0 3px rgba(0,0,0,.12)}
.feature-divider{position:absolute;top:0;width:1px;height:164px;background:#e0e0e0}
.feature-photo{position:absolute;top:39px;width:122px;height:92px;background:linear-gradient(180deg,#5d7bb0 0%,#d79a5c 60%,#1c1f2c 100%)}
.feature-title{position:absolute;top:40px;font-size:18px;font-weight:700;color:var(--title-red)}
.feature-text{position:absolute;top:73px;width:210px;font-size:12.5px;line-height:17px;color:#555}
.traveller-figure{position:absolute;left:755px;top:26px;width:76px;height:100px;background:#9b1016;border-radius:6px}
.no-fees-title{position:absolute;left:844px;top:28px;font-size:29px;font-weight:700;color:var(--fees-blue)}
.no-fees-text{position:absolute;left:844px;top:61px;width:140px;font-size:16px;line-height:22px;color:#111}

/* social */
.social-bar{position:absolute;left:607px;top:751px;display:flex;align-items:center;font-family:Arial,sans-serif;font-size:11px;color:#333}
.social-btn{height:22px;line-height:20px;padding:0 6px;border:1px solid #c4cde0;background:#eef1f8;border-radius:2px;color:#3b5998;margin-right:8px}
.social-count a{color:#3b5998;text-decoration:none}

/* story */
.story{position:absolute;left:30px;top:763px;width:572px}
.story-title{font-family:"Questrial",sans-serif;font-weight:400;font-size:27px;line-height:34px;color:var(--story-blue)}
.story-text{margin-top:0;font-size:16px;line-height:24px;color:#4b4b4b}
.story-link{margin-top:14px;margin-left:2px;font-size:17px;line-height:26px;color:var(--link-plum);display:flex;align-items:center;gap:6px}

/* city band */
.city-band{position:absolute;left:0;top:0}
.site-footer{position:absolute;right:48px;top:1145px;font-size:13px;color:var(--yellow)}
</style>
</head>
<body>
<div class="frame"></div>

<header class="site-header">
  <div class="brand"><span class="brand-dot"></span><span class="brand-name">Rovelink.co.uk</span></div>
  <svg class="car-icon" width="50" height="48" viewBox="0 0 50 48" aria-hidden="true">
    <rect x="18" y="2" width="14" height="6" rx="2" fill="#fff"/>
    <path d="M10 22 L15 10 H35 L40 22 Z" fill="#fff"/>
    <path d="M14 21 L17.5 13 H32.5 L36 21 Z" fill="#c20b0d"/>
    <rect x="3" y="21" width="44" height="16" rx="5" fill="#fff"/>
    <circle cx="12" cy="29" r="3" fill="#c20b0d"/><circle cx="38" cy="29" r="3" fill="#c20b0d"/>
    <rect x="7" y="36" width="8" height="8" rx="2" fill="#fff"/><rect x="35" y="36" width="8" height="8" rx="2" fill="#fff"/>
  </svg>
  <div class="booking-line"><span class="number">020 7946 0318:</span> <span class="label">Booking Line</span></div>
</header>

<nav class="main-nav">
  <ul>
    <li class="active">HOME</li>
    <li>ROVELINK MILES</li>
    <li>JOIN US</li>
    <li>ABOUT US</li>
    <li>CONTACT</li>
  </ul>
</nav>

<div class="hero-photo" role="img" aria-label="Photo of Tower Bridge in London lit up at dusk with the city skyline"></div>
<p class="hero-tagline"><span class="line-1">As easy as opening the cab's door</span><span class="line-2">Its free, dependable and with no obligation</span></p>

<div class="booking-tabs">
  <span class="tab-book">BOOK A CAB</span>
  <span class="tab-tour">CITY TOUR</span>
  <span class="tab-account">YOUR ACCOUNT</span>
</div>
<form class="booking-panel">
  <div class="field f-from">Pick me up from:
    <svg width="10" height="14" viewBox="0 0 10 14"><path d="M5 0a5 5 0 0 1 5 5c0 3.5-5 9-5 9S0 8.5 0 5a5 5 0 0 1 5-5z" fill="#111"/><circle cx="5" cy="5" r="1.8" fill="#f4f4f8"/></svg></div>
  <div class="field f-to">Drop me at:
    <svg width="10" height="14" viewBox="0 0 10 14"><path d="M5 0a5 5 0 0 1 5 5c0 3.5-5 9-5 9S0 8.5 0 5a5 5 0 0 1 5-5z" fill="#111"/><circle cx="5" cy="5" r="1.8" fill="#f4f4f8"/></svg></div>
  <div class="field f-date">Pick up date and time
    <svg width="16" height="15" viewBox="0 0 16 15"><rect x="1" y="2" width="14" height="12" fill="none" stroke="#111" stroke-width="1.6"/><rect x="1" y="2" width="14" height="3" fill="#111"/><rect x="4" y="0" width="2" height="4" fill="#111"/><rect x="10" y="0" width="2" height="4" fill="#111"/><text x="8" y="12.5" font-size="7" text-anchor="middle" font-family="Arial,sans-serif" font-weight="700" fill="#111">5</text></svg></div>
  <div class="field f-pass">number of passengers
    <svg width="8" height="12" viewBox="0 0 8 12"><path d="M1 1 L6 6 L1 11" stroke="#111" stroke-width="2" fill="none"/></svg></div>
  <div class="field f-kids">Kids
    <svg width="8" height="12" viewBox="0 0 8 12"><path d="M1 1 L6 6 L1 11" stroke="#111" stroke-width="2" fill="none"/></svg></div>
  <div class="contact-box">
    <div class="contact-field cf-name">your name</div>
    <div class="contact-field cf-addr">your address</div>
    <div class="contact-field cf-phone">your phone number</div>
  </div>
  <div class="enter-button">enter here</div>
</form>

<section class="features">
  <div class="feature-photo" style="left:20px" role="img" aria-label="Photo of the London skyline at sunset"></div>
  <h3 class="feature-title" style="left:158px">Why Rovelink ?</h3>
  <p class="feature-text" style="left:160px">Rovelink guarantees that you get the best deal for your travel, as you get quotes from several cab companies.</p>
  <div class="feature-divider" style="left:366px"></div>
  <div class="feature-photo" style="left:390px" role="img" aria-label="Photo of the London skyline at sunset"></div>
  <h3 class="feature-title" style="left:528px">Why Rovelink ?</h3>
  <p class="feature-text" style="left:530px">Rovelink guarantees that you get the best deal for your travel, as you get quotes from several cab companies.</p>
  <div class="feature-divider" style="left:749px"></div>
  <div class="traveller-figure" role="img" aria-label="Illustration of a traveller with a suitcase hailing a cab"></div>
  <h3 class="no-fees-title">No fees</h3>
  <p class="no-fees-text">There's absolutely no cost for you to use our service</p>
</section>

<svg class="city-band" width="1024" height="1200" role="img" aria-label="Photo of the London city skyline at night in magenta tones">
  <defs>
    <linearGradient id="cityTone" x1="0" y1="0" x2="0" y2="1">
      <stop offset="0" stop-color="#8a2a6a"/>
      <stop offset="0.45" stop-color="#a0205a"/>
      <stop offset="0.75" stop-color="#4a0f2c"/>
      <stop offset="1" stop-color="#1e0812"/>
    </linearGradient>
  </defs>
  <path d="M23 1015 Q 470 1150 996 790 L996 1178 L23 1178 Z" fill="url(#cityTone)"/>
</svg>

<div class="social-bar">
  <span class="social-btn">Like</span>
  <span class="social-btn">Send</span>
  <span class="social-count">277 likes. <a>Sign Up</a> to see what your friends like.</span>
</div>

<section class="story">
  <h2 class="story-title">The best stories from our community</h2>
  <p class="story-text">&nbsp;I recently hit London for a girlie night on the town with my bestie. After a little too much champagne, we had a stupid argument and decided to leave the club early. In the cab on our way home, we didn't say one word to each other. The driver who could sense we were both upset however, had other plans. He randomly started singing Vela's Disco Moon! My best friend and I were in shock, we looked at each other and couldn't stop laughing! The remainder of the journey consisted of us all belting out Vela classics, in between fits of laughter. We were so disappointed when we arrived home as we wanted to continue the fun, we will never forget our singing taxi driver!</p>
  <div class="story-link">click HERE to send us your story
    <svg width="22" height="28" viewBox="0 0 22 28"><path d="M4 3 L16 14 L4 25" stroke="#ffd52b" stroke-width="5" fill="none" stroke-linecap="round" stroke-linejoin="round"/></svg>
  </div>
</section>

<footer class="site-footer">2011-12 Rovelink | Company info | Privacy Policy</footer>
</body>
</html>
```